Floor Inspections and Consulting

We provide inspections and consulting services on various floor coverings, e.g. carpet, hardwood, etc. We also do expert witness work for attorneys due to floor covering failures. We current have a logo, just need it incorporated into a new design. I have examples of cards I have found on the internet that capture my attention and make a statement. I have included our original business card, which in my opinion is terrible, but it does have our logo on it.

```html
<!DOCTYPE html>
<html lang="en">
<head>
<meta charset="utf-8">
<title>Keystone Floor Reviews – Business Card</title>
<link href="https://fonts.googleapis.com/css2?family=Archivo:wght@400;500;700&display=swap" rel="stylesheet">
<style>
  :root{
    --backdrop:#2f2723;
    --wood-light:#d6ad78;
    --wood-mid:#c39462;
    --wood-dark:#a87a4c;
    --ink:#6a4a32;
    --ink-soft:#7d5a3f;
    --rule:rgba(106,74,50,.45);
  }
  *{box-sizing:border-box;margin:0;padding:0}
  html,body{width:1200px;height:844px;overflow:hidden}
  body{background:var(--backdrop);font-family:"Archivo",Arial,sans-serif;color:var(--ink);position:relative}
  .card{
    position:absolute;top:273px;width:520px;height:298px;
    box-shadow:0 14px 30px rgba(0,0,0,.45);overflow:hidden;
  }
  .card--back{left:50px}
  .card--front{left:630px}
  .wood{
    position:absolute;inset:0;
    background:
      linear-gradient(180deg,rgba(255,255,255,.08),rgba(0,0,0,.06)),
      linear-gradient(100deg,var(--wood-mid) 0%,var(--wood-light) 45%,var(--wood-mid) 75%,var(--wood-dark) 100%);
  }
  .content{position:absolute;inset:0}

  /* back side */
  .brand-block{
    position:absolute;left:40px;top:0;bottom:0;width:210px;
    display:flex;flex-direction:column;justify-content:center;align-items:center;gap:12px;
  }
  .brand-mark{width:22px;height:22px;background:var(--ink)}
  .brand-name{
    font-weight:700;font-size:22px;line-height:1.15;text-transform:uppercase;text-align:center;color:var(--ink);
  }
  .divider{position:absolute;left:268px;top:56px;bottom:56px;width:1px;background:var(--rule)}
  .contact{position:absolute;left:288px;top:82px;right:20px}
  .contact-name{font-weight:700;font-size:18px;letter-spacing:.06em;text-transform:uppercase;margin-bottom:16px}
  .contact-row{display:flex;align-items:center;gap:8px;font-size:14px;margin-bottom:9px;color:var(--ink-soft)}
  .contact-row svg{width:14px;height:14px;flex:none}

  /* front side */
  .front-block{
    position:absolute;inset:0;display:flex;flex-direction:column;align-items:center;justify-content:center;gap:10px;
  }
  .front-block .brand-mark{width:26px;height:26px}
  .front-block .brand-name{font-size:28px}
  .tagline{font-size:11px;font-weight:500;letter-spacing:.18em;text-transform:uppercase;color:var(--ink-soft)}
  .service-line{margin-top:14px;font-size:14px;font-weight:500;letter-spacing:.03em;color:var(--ink)}
</style>
</head>
<body>

<section class="card card--back">
  <div class="wood" role="img" aria-label="Light oak wood plank texture"></div>
  <div class="content">
    <div class="brand-block">
      <span class="brand-mark"></span>
      <p class="brand-name">Keystone<br>Floor Reviews</p>
    </div>
    <span class="divider"></span>
    <div class="contact">
      <p class="contact-name">Dana Merrow</p>
      <p class="contact-row">
        <svg viewBox="0 0 16 16"><rect x="0.5" y="0.5" width="15" height="15" rx="2" fill="none" stroke="currentColor"/><path d="M5 4c-1 1-1 3 1 5s4 3 5 2l-1.5-1.5-1 .7c-1-.5-2-1.5-2.5-2.5l.7-1z" fill="currentColor"/></svg>
        555-014-2290
      </p>
      <p class="contact-row">
        <svg viewBox="0 0 16 16"><rect x="1" y="3" width="14" height="10" fill="currentColor"/><path d="M1 3l7 6 7-6" fill="none" stroke="#d6ad78" stroke-width="1.2"/></svg>
        dana@keystonefloors.com
      </p>
      <p class="contact-row">
        <svg viewBox="0 0 16 16"><circle cx="8" cy="8" r="7" fill="none" stroke="currentColor" stroke-width="1.4"/><ellipse cx="8" cy="8" rx="3" ry="7" fill="none" stroke="currentColor"/><path d="M1 8h14" stroke="currentColor"/></svg>
        www.keystonefloors.com
      </p>
    </div>
  </div>
</section>

<section class="card card--front">
  <div class="wood" role="img" aria-label="Light oak wood plank texture"></div>
  <div class="content front-block">
    <span class="brand-mark"></span>
    <p class="brand-name">Keystone Floor Reviews</p>
    <p class="tagline">Analysis &amp; Consulting</p>
    <p class="service-line">Certified Floor Covering Inspection &amp; Consulting</p>
  </div>
</section>

</body>
</html>
```